Business Card Design

I already have a company logo for my company. I have a logo for the manufacturer we represent. I want a professional business card design.

```html
<!DOCTYPE html>
<html lang="en">
<head>
<meta charset="utf-8">
<title>Beacon Alert Group – Business Card</title>
<link rel="stylesheet" href="https://fonts.googleapis.com/css2?family=Open+Sans:wght@400;600;700&display=swap">
<style>
  :root {
    --backdrop: #232323;
    --card: #1e1e22;
    --gold: #b98d2c;
    --red: #e3202a;
    --white: #ffffff;
    --silver: #d2d2d4;
    --text-font: "Open Sans", Arial, sans-serif;
  }
  html, body {
    margin: 0;
    padding: 0;
    width: 1200px;
    height: 780px;
    overflow: hidden;
    background: var(--backdrop);
    font-family: var(--text-font);
  }
  .canvas {
    width: 1200px;
    height: 780px;
    display: flex;
    align-items: center;
    justify-content: center;
    gap: 40px;
  }
  .card {
    position: relative;
    width: 540px;
    height: 310px;
    border-radius: 22px;
    background: var(--card);
    overflow: hidden;
    box-shadow: 0 14px 30px rgba(0,0,0,0.45);
  }
  .card-front .swoop {
    position: absolute;
    inset: 0;
    width: 100%;
    height: 100%;
  }
  .holder {
    position: absolute;
    left: 42px;
    top: 40px;
  }
  .holder-name {
    margin: 0;
    font-size: 28px;
    font-weight: 700;
    line-height: 1.1;
  }
  .holder-name .first { color: var(--gold); }
  .holder-name .last { color: var(--red); }
  .holder-title {
    margin: 6px 0 0 2px;
    font-size: 13px;
    color: var(--white);
  }
  .brand {
    position: absolute;
    display: flex;
    align-items: center;
    gap: 10px;
    font-weight: 700;
    text-transform: uppercase;
    letter-spacing: 0.04em;
  }
  .brand-front {
    right: 34px;
    top: 46px;
    font-size: 17px;
    color: var(--white);
  }
  .brand-dot {
    width: 26px;
    height: 26px;
    border-radius: 50%;
    background: var(--red);
  }
  .divider {
    position: absolute;
    left: 272px;
    top: 100px;
    width: 2px;
    height: 84px;
    background: var(--gold);
  }
  .contacts {
    position: absolute;
    left: 292px;
    top: 104px;
    margin: 0;
    padding: 0;
    list-style: none;
    color: var(--white);
    font-size: 14px;
  }
  .contacts li {
    display: flex;
    align-items: center;
    gap: 10px;
    height: 26px;
  }
  .contacts svg {
    width: 15px;
    height: 15px;
    fill: var(--gold);
  }
  .address {
    position: absolute;
    left: 70px;
    bottom: 18px;
    margin: 0;
    font-size: 15px;
    color: var(--white);
  }
  .card-back {
    display: flex;
    align-items: center;
    justify-content: center;
  }
  .brand-back {
    position: static;
    font-size: 30px;
    color: var(--silver);
    gap: 16px;
  }
  .brand-back .brand-dot {
    width: 44px;
    height: 44px;
    background: var(--silver);
  }
</style>
</head>
<body>
<main class="canvas">
  <section class="card card-front" aria-label="Card front">
    <svg class="swoop" viewBox="0 0 540 310" preserveAspectRatio="none" aria-hidden="true">
      <path d="M0,150 Q40,250 260,262 Q420,270 540,238 L540,310 L0,310 Z" fill="var(--gold)"/>
      <path d="M22,138 Q70,238 270,250 Q420,258 540,228" fill="none" stroke="var(--red)" stroke-width="3"/>
    </svg>

    <div class="holder">
      <h1 class="holder-name"><span class="first">Marlena</span> <span class="last">Vostra</span></h1>
      <p class="holder-title">Managing Director</p>
    </div>

    <div class="brand brand-front">
      <span class="brand-dot"></span>
      <span class="brand-name">Beacon Alert Group</span>
    </div>

    <div class="divider"></div>

    <ul class="contacts">
      <li>
        <svg viewBox="0 0 24 24" aria-hidden="true"><path d="M6.6 10.8a15.1 15.1 0 0 0 6.6 6.6l2.2-2.2a1 1 0 0 1 1-.25 11.4 11.4 0 0 0 3.6.57 1 1 0 0 1 1 1V20a1 1 0 0 1-1 1A17 17 0 0 1 3 4a1 1 0 0 1 1-1h3.5a1 1 0 0 1 1 1c0 1.25.2 2.45.57 3.6a1 1 0 0 1-.25 1z"/></svg>
        <span>(555) 214-3080</span>
      </li>
      <li>
        <svg viewBox="0 0 24 24" aria-hidden="true"><path d="M2 5h20v14H2z M4 7v.4l8 5 8-5V7l-8 5z" fill-rule="evenodd"/></svg>
        <span>info@beaconalert.com</span>
      </li>
      <li>
        <svg viewBox="0 0 24 24" aria-hidden="true"><path d="M12 2a10 10 0 1 0 0 20 10 10 0 0 0 0-20zm0 2c.9 1.2 1.6 2.8 1.9 5h-3.8c.3-2.2 1-3.8 1.9-5zM4.3 14a8 8 0 0 1 0-4h3.8a17 17 0 0 0 0 4zm.9 2h3.2a11 11 0 0 0 1.3 3.6A8 8 0 0 1 5.2 16zm3.2-8H5.2a8 8 0 0 1 4.5-3.6A11 11 0 0 0 8.4 8zM12 20c-.9-1.2-1.6-2.8-1.9-4h3.8c-.3 1.2-1 2.8-1.9 4zm2.1-6H9.9a15 15 0 0 1 0-4h4.2a15 15 0 0 1 0 4zm.2 5.6a11 11 0 0 0 1.3-3.6h3.2a8 8 0 0 1-4.5 3.6zM15.9 14a17 17 0 0 0 0-4h3.8a8 8 0 0 1 0 4zm-.3-6a11 11 0 0 0-1.3-3.6A8 8 0 0 1 18.8 8z"/></svg>
        <span>www.beaconalert.com</span>
      </li>
    </ul>

    <p class="address">418 Harlow Ave. Suite 120 Millbrook, TX 75019</p>
  </section>

  <section class="card card-back" aria-label="Card back">
    <div class="brand brand-back">
      <span class="brand-dot"></span>
      <span class="brand-name">Beacon Alert Group</span>
    </div>
  </section>
</main>
</body>
</html>
```